Defense contractor needs a roll-up for an exhibition

The booth we have booked has only a size of 3m².
So this will be the centerpiece of the whole booth.
We need a roll-up that attracts visitors and at the same time it should contain already designed graphics. These graphics are giving visitors an overview of our system. So it is necessary to have them exposed in a height that the booth personal can conveniently point with its fingers at them.
For information about our company and product visit:
https://www.brellowtrackline.com/
For designing you should use Adobe Illustrator and the templates provided in the zip file, to guarantee a perfect print.
I have supplied my business card that you can copy the logo. As the company logo will be already at the booth nearby the top of the roll-up, you should not place it there. It can be in the middle or at the bottom.
I have uploaded a picture of the booth. The roll up will be placed at the left of the screen and has a size of 80cm x 200cm

Defense

Defense

Serif

0054AA
0677BA
7BADD7
CADEEF
E8F1F8

• you must use the Adobe Illustrator template to have a good printing result
• company logo on the upper side of the roll-up

```html
<!DOCTYPE html>
<html lang="en">
<head>
<meta charset="utf-8">
<title>Brellow Trackline – Roll-up</title>
<link rel="stylesheet" href="https://fonts.googleapis.com/css2?family=Saira+Semi+Condensed:wght@400;700&family=Montserrat:wght@400;600;700&display=swap">
<style>
  :root {
    --page-bg: #efefef;
    --navy: #0c1a5b;
    --navy-deep: #07113d;
    --green: #6c9163;
    --white: #ffffff;
    --ink: #111111;
    --panel-tint: #e6e8f6;
  }
  html, body {
    margin: 0;
    width: 800px;
    height: 1200px;
    overflow: hidden;
    background: var(--page-bg);
  }
  .rollup {
    position: absolute;
    left: 168px;
    top: 30px;
    width: 463px;
    height: 1140px;
    box-shadow: 0 10px 30px rgba(0,0,0,0.18);
  }
  .rollup svg { display: block; width: 100%; height: 100%; }
  .brand-name { font-family: "Montserrat", sans-serif; font-weight: 700; fill: var(--ink); text-anchor: middle; }
  .headline { font-family: "Saira Semi Condensed", "Arial Narrow", sans-serif; text-anchor: middle; }
  .headline-light { font-weight: 400; fill: var(--white); }
  .headline-green { font-weight: 700; fill: var(--green); }
  .headline-white { font-weight: 700; fill: var(--white); }
  .section-label { font-family: "Saira Semi Condensed", "Arial Narrow", sans-serif; font-weight: 700; fill: var(--white); text-anchor: middle; }
  .tagline { font-family: "Montserrat", sans-serif; font-weight: 400; fill: var(--white); text-anchor: middle; }
  .service { font-family: "Montserrat", sans-serif; font-weight: 700; fill: var(--white); }
  .phone { font-family: "Montserrat", sans-serif; font-weight: 700; fill: var(--white); }
  .web { font-family: "Montserrat", sans-serif; font-weight: 600; fill: var(--ink); text-anchor: middle; }
</style>
</head>
<body>
<div class="rollup">
  <svg viewBox="0 0 506 1245" xmlns="http://www.w3.org/2000/svg">
    <defs>
      <linearGradient id="skyTones" x1="0" y1="0" x2="1" y2="1">
        <stop offset="0" stop-color="#3a5a9c"/>
        <stop offset="0.5" stop-color="#1f3a78"/>
        <stop offset="1" stop-color="#141a2c"/>
      </linearGradient>
      <radialGradient id="fireGlow" cx="0.28" cy="0.5" r="0.5">
        <stop offset="0" stop-color="#ffd23a"/>
        <stop offset="0.35" stop-color="#f39a1c"/>
        <stop offset="0.7" stop-color="#c86a4a" stop-opacity="0.6"/>
        <stop offset="1" stop-color="#c86a4a" stop-opacity="0"/>
      </radialGradient>
      <radialGradient id="smokeGlow" cx="0.2" cy="0.25" r="0.35">
        <stop offset="0" stop-color="#d99a8c" stop-opacity="0.8"/>
        <stop offset="1" stop-color="#d99a8c" stop-opacity="0"/>
      </radialGradient>
      <linearGradient id="groundShade" x1="0" y1="0" x2="0" y2="1">
        <stop offset="0.55" stop-color="#2a2d2a" stop-opacity="0"/>
        <stop offset="1" stop-color="#3b3f3a" stop-opacity="0.85"/>
      </linearGradient>
      <linearGradient id="panelTone" x1="0" y1="0" x2="0" y2="1">
        <stop offset="0" stop-color="#eef0fa"/>
        <stop offset="1" stop-color="#dcdfef"/>
      </linearGradient>
      <radialGradient id="panelShade" cx="0.5" cy="0.55" r="0.5">
        <stop offset="0" stop-color="#b9bccb" stop-opacity="0.55"/>
        <stop offset="1" stop-color="#b9bccb" stop-opacity="0"/>
      </radialGradient>
    </defs>

    <!-- page -->
    <rect class="sheet" width="506" height="1245" fill="var(--white)"/>

    <!-- brand header -->
    <text class="brand-name" x="253" y="76" font-size="30">BRELLOW TRACKLINE</text>
    <polygon class="header-wedge" points="8,122 506,100 506,120 8,124" fill="var(--ink)"/>

    <!-- hero image area -->
    <g class="hero" role="img" aria-label="Photo of a battle tank in flames under a dark blue sky">
      <rect x="0" y="126" width="506" height="364" fill="url(#skyTones)"/>
      <rect x="0" y="126" width="506" height="364" fill="url(#smokeGlow)"/>
      <rect x="0" y="126" width="506" height="364" fill="url(#fireGlow)"/>
      <rect x="0" y="126" width="506" height="364" fill="url(#groundShade)"/>
    </g>
    <polygon class="hero-cut-line" points="506,270 424,490 432,490 506,292" fill="var(--white)"/>
    <polygon class="hero-cut" points="506,292 432,490 506,490" fill="var(--ink)"/>

    <!-- divider band -->
    <rect class="divider" x="0" y="497" width="506" height="15" fill="var(--navy)"/>

    <!-- system overview graphics -->
    <g class="overview-left" role="img" aria-label="Illustration of a training classroom with instructor screens and trainee workstations">
      <rect x="0" y="512" width="262" height="158" fill="url(#panelTone)"/>
      <rect x="0" y="512" width="262" height="158" fill="url(#panelShade)"/>
    </g>
    <g class="overview-right" role="img" aria-label="Illustration of simulated tanks, targets and a mobile training truck with crew">
      <rect x="250" y="512" width="256" height="158" fill="url(#panelTone)"/>
      <rect x="250" y="512" width="256" height="158" fill="url(#panelShade)"/>
    </g>
    <polygon class="overview-split" points="257,512 273,512 214,670 198,670" fill="var(--navy)"/>

    <!-- information panel -->
    <rect class="info-panel" x="0" y="670" width="506" height="495" fill="var(--navy)"/>

    <text class="headline headline-light" x="253" y="724" font-size="27" textLength="246" lengthAdjust="spacingAndGlyphs">ADVANCED COMBAT</text>
    <text class="headline headline-green" x="253" y="764" font-size="40" textLength="352" lengthAdjust="spacingAndGlyphs">TRAINING SYSTEMS</text>
    <text class="headline headline-white" x="253" y="802" font-size="38" textLength="248" lengthAdjust="spacingAndGlyphs">FOR REALISTIC</text>
    <text class="headline headline-green" x="253" y="843" font-size="42" textLength="427" lengthAdjust="spacingAndGlyphs">COMBAT SIMULATION</text>

    <!-- services label -->
    <line x1="30" y1="898" x2="476" y2="898" stroke="var(--navy-deep)" stroke-width="2"/>
    <path class="services-ribbon" d="M108,878 H400 Q384,884 376,918 H136 Q126,884 108,878 Z" fill="var(--green)"/>
    <text class="section-label" x="253" y="909" font-size="25" textLength="171" lengthAdjust="spacingAndGlyphs">OUR SERVICES</text>

    <text class="tagline" x="253" y="950" font-size="16" textLength="442" lengthAdjust="spacingAndGlyphs">The signature of the contract is not the end - it is just</text>
    <text class="tagline" x="253" y="970" font-size="16" textLength="361" lengthAdjust="spacingAndGlyphs">the beginning of a long-lasting partnership.</text>

    <!-- services list -->
    <g class="service-list">
      <g class="tick" transform="translate(47,1001)"><circle r="6.5" fill="var(--green)"/><path d="M-3,0 L-1,2.5 L3,-2.5" stroke="var(--navy)" stroke-width="1.8" fill="none"/></g>
      <text class="service" x="64" y="1007" font-size="16">Extended warranty</text>
      <text class="service" x="64" y="1027" font-size="16">programs</text>

      <g class="tick" transform="translate(47,1062)"><circle r="6.5" fill="var(--green)"/><path d="M-3,0 L-1,2.5 L3,-2.5" stroke="var(--navy)" stroke-width="1.8" fill="none"/></g>
      <text class="service" x="64" y="1068" font-size="16">Logistics support</text>

      <g class="tick" transform="translate(47,1102)"><circle r="6.5" fill="var(--green)"/><path d="M-3,0 L-1,2.5 L3,-2.5" stroke="var(--navy)" stroke-width="1.8" fill="none"/></g>
      <text class="service" x="64" y="1108" font-size="16">Maintenance contracts</text>

      <g class="tick" transform="translate(276,1001)"><circle r="6.5" fill="var(--green)"/><path d="M-3,0 L-1,2.5 L3,-2.5" stroke="var(--navy)" stroke-width="1.8" fill="none"/></g>
      <text class="service" x="294" y="1007" font-size="16">long-term spare</text>
      <text class="service" x="294" y="1027" font-size="16">part services to</text>
      <text class="service" x="294" y="1047" font-size="16">keep the equipment</text>
      <text class="service" x="294" y="1067" font-size="16">in perfect</text>
      <text class="service" x="294" y="1087" font-size="16">operational</text>
      <text class="service" x="294" y="1107" font-size="16">condition</text>
    </g>

    <!-- phone pill -->
    <rect class="phone-pill" x="92" y="1140" width="322" height="40" rx="20" fill="var(--green)"/>
    <g class="phone-icon" transform="translate(114,1160)">
      <circle r="14" fill="var(--white)"/>
      <path d="M-6,-6 Q-7,-1 -2,4 Q3,8 7,6 L7,3 L3,1 L1,3 Q-3,1 -4,-2 L-2,-3 L-4,-7 Z" fill="var(--navy)"/>
    </g>
    <text class="phone" x="140" y="1171" font-size="29" textLength="258" lengthAdjust="spacingAndGlyphs">49 1570 2246813</text>

    <!-- web address -->
    <text class="web" x="253" y="1212" font-size="17" textLength="303" lengthAdjust="spacingAndGlyphs">www.brellowtrackline.com</text>
  </svg>
</div>
</body>
</html>
```